Audio/ Video Packaging Design for a Technology company.

We need a packaging design for a bag that is 7" wide and 10" high. The design will be for a new line of audio/video products. We would like to see designs that represent a superior quality product that provides a pure connection. We want the equivalent of a nice retail bag that you would find in a store like Tallow Mart. It should be a maximum of three colors. We really want something sharp, professional and eye catching, not whimsical or cartoonish. I've included a couple of examples below. I don't really like the designs of the bags, but I want you to see examples of what I'm looking for.

The company logo, which is uploaded, should be on the design. The words "audio and video products" should be either underneath the logo or to the side. Also, somewhere on the bag, we would like the words "For a Pure Connection"

The winner of this contest will likely get the opportunity for additional work as we have more products ready to launch.

Target Market(s)

resellers, consumers - men 25-60

Industry/Entity Type

It Company

Requirements
Must have
• It should be a maximum of three colors. We really want something sharp, professional and eye catching, not whimsical or cartoonish
Nice to have
• Eye-catching design. Utilize the entire bag but don't make it too busy.
Should not have
• Whimsical, cartoonish

```html
<!DOCTYPE html>
<html lang="en">
<head>
<meta charset="utf-8">
<title>Veridon Audio and Video Products – Bag Packaging</title>
<link rel="stylesheet" href="https://fonts.googleapis.com/css2?family=Montserrat:wght@500&family=Quicksand:wght@500&family=PT+Sans+Narrow:wght@700&display=swap">
<style>
  :root {
    --backdrop: #dfe6ee;
    --bag-blue: #1f86c6;
    --bag-deep: #1b5d9e;
    --bag-panel: #1c7cbc;
    --navy: #1c2a55;
    --accent: #2a6db5;
    --white: #ffffff;
    --pale: #eef3f8;
  }
  * { margin: 0; padding: 0; box-sizing: border-box; }
  html, body { width: 1200px; height: 787px; overflow: hidden; }
  body { background: var(--backdrop); position: relative; }

  .bag {
    position: absolute;
    top: 106px;
    width: 438px;
    height: 624px;
    border-radius: 26px;
    background: linear-gradient(160deg, var(--bag-blue), var(--bag-deep));
  }
  .bag--front { left: 144px; }
  .bag--back { left: 616px; }

  .bag__window {
    position: absolute;
    left: 22px; top: 22px;
    width: 394px; height: 550px;
    background: var(--white);
    border-radius: 14px 14px 0 0;
    overflow: hidden;
  }
  .bag__panel {
    position: absolute;
    left: 22px; top: 22px;
    width: 394px; height: 580px;
    border-radius: 22px;
    background: linear-gradient(170deg, #1f93d0 0%, var(--bag-panel) 45%, var(--bag-deep) 100%);
  }

  .zip-line {
    position: absolute;
    left: 0; right: 0;
    height: 2px;
  }
  .bag__window .zip-line { background: #e4e8ee; }
  .bag__panel .zip-line { background: rgba(20, 70, 130, 0.55); }

  .hang-tab {
    position: absolute;
    left: 72px; top: -22px;
    width: 250px; height: 116px;
    border-radius: 0 0 22px 22px;
    background: linear-gradient(180deg, var(--bag-blue), var(--bag-deep));
  }
  .hang-slot { position: absolute; width: 104px; height: 26px; }

  .brand {
    position: absolute;
    left: 0; right: 0;
    text-align: center;
  }
  .brand__disc {
    display: block;
    margin: 0 auto;
    width: 92px; height: 92px;
    border-radius: 50%;
  }
  .brand__name {
    display: block;
    font-family: "Montserrat", sans-serif;
    font-weight: 500;
    font-size: 46px;
    letter-spacing: 2px;
    line-height: 1;
  }
  .tagline {
    display: block;
    font-family: "Quicksand", sans-serif;
    font-weight: 500;
    font-size: 21px;
    line-height: 1;
  }

  .bag--front .brand { top: 96px; }
  .bag--front .brand__disc { background: var(--pale); border: 2px solid #d7dde6; }
  .bag--front .brand__name { color: var(--navy); margin-top: 34px; }
  .bag--front .tagline { color: var(--navy); margin-top: 14px; }
  .tagline__accent { color: var(--accent); }

  .bag--back .brand { top: 82px; }
  .bag--back .brand__disc { background: var(--white); }
  .bag--back .brand__name { color: var(--white); margin-top: 40px; }
  .bag--back .tagline { color: var(--white); margin-top: 22px; }

  .pattern-field {
    position: absolute;
    left: 0; top: 288px;
    width: 394px; height: 262px;
    background: linear-gradient(160deg, #ffffff 20%, #cfe3f3 55%, #7fb2de 100%);
  }

  .slogan {
    position: absolute;
    left: 0; right: 0; top: 580px;
    text-align: center;
    font-family: "PT Sans Narrow", sans-serif;
    font-weight: 700;
    font-size: 28px;
    color: var(--white);
  }

  .origin {
    position: absolute;
    right: 66px; top: 508px;
    font-family: "PT Sans Narrow", sans-serif;
    font-weight: 700;
    font-size: 13px;
    color: var(--white);
  }
  .cert-badges {
    position: absolute;
    right: 18px; top: 532px;
    display: flex;
    gap: 17px;
  }
  .cert-badge {
    width: 32px; height: 32px;
    border-radius: 50%;
    background: var(--white);
    border: 3px solid #c9d6e4;
  }
</style>
</head>
<body>

  <section class="bag bag--front" aria-label="Front of bag">
    <div class="bag__window">
      <div class="zip-line" style="top:90px"></div>
      <div class="zip-line" style="top:100px"></div>
      <div class="pattern-field" role="img" aria-label="Pixel mosaic of light and mid blue squares forming a V shape"></div>
    </div>
    <div class="hang-tab">
      <svg class="hang-slot" style="left:73px;top:32px" viewBox="0 0 104 26" aria-hidden="true">
        <path d="M13 4 H40 Q44 4 46 1 Q52 -3 58 1 Q60 4 64 4 H91 A9 9 0 0 1 91 22 H13 A9 9 0 0 1 13 4 Z" fill="#ffffff"/>
      </svg>
    </div>
    <div class="brand">
      <span class="brand__disc"></span>
      <span class="brand__name">VERIDON</span>
      <span class="tagline">Audio and Video <span class="tagline__accent">Products</span></span>
    </div>
    <p class="slogan">For a Pure Connection</p>
  </section>

  <section class="bag bag--back" aria-label="Back of bag">
    <div class="bag__panel">
      <div class="zip-line" style="top:68px"></div>
      <div class="zip-line" style="top:76px"></div>
      <div class="zip-line" style="top:84px"></div>
      <svg class="hang-slot" style="left:145px;top:13px" viewBox="0 0 104 26" aria-hidden="true">
        <path d="M13 4 H40 Q44 4 46 1 Q52 -3 58 1 Q60 4 64 4 H91 A9 9 0 0 1 91 22 H13 A9 9 0 0 1 13 4 Z" fill="#ffffff"/>
      </svg>
      <div class="brand">
        <span class="brand__disc"></span>
        <span class="brand__name">VERIDON</span>
        <span class="tagline">Audio and Video Products</span>
      </div>
      <p class="origin">MADE IN CHINA</p>
      <div class="cert-badges">
        <span class="cert-badge"></span>
        <span class="cert-badge"></span>
        <span class="cert-badge"></span>
      </div>
    </div>
  </section>

</body>
</html>
```